Business Card for Multi-Brand Sportswear Company

We are looking for a business card which represents our company and the multiple brands within it.

The company: Fen Athletics (LTD)
The brands: Fen, TavaPuni, ElmStretch, Grit and Rain

Employees using these cards would be representing Fen Athletics, rather than any of the individual brands. You will see a current design within the uploaded files, to give some inspiration. The actual text of the brands is not necessary, but the logos should be on there is some format.

Our creative minds on this are stretched, so we are looking for someone to make this their own, and show us what a good business card should look like.

We may like to get these printed with spot gloss, so keep that in mind with your designs.

www.fenathletics.co.uk

Industry/Entity Type

Business

Contact Information for Business Card

Leo Pemberton-Hale
Operations Manager
(+44) 1632 960 418
Leo@fenathletics.co.uk
www.fenathletics.co.uk

Font styles to use
Sans Serif
Other font styles liked:
• Eurostile

Colors
ffffff

Requirements
Nice to have
• Dark (black) background

```html
<!DOCTYPE html>
<html lang="en">
<head>
<meta charset="utf-8">
<title>Fen Athletics – Business Card</title>
<link rel="stylesheet" href="https://fonts.googleapis.com/css2?family=Exo+2:ital,wght@0,400;0,500;0,600;0,700;1,400&display=swap">
<style>
  :root {
    --backdrop: #3b3b3b;
    --card-white: #ffffff;
    --card-black: #000000;
    --ink: #111111;
    --ink-soft: #6b6b6b;
    --accent-red: #e3262b;
    --brand-grey: #9a9a9a;
    --brand-plum: #6b5a70;
  }
  * { margin: 0; padding: 0; box-sizing: border-box; }
  html, body {
    width: 1105px;
    height: 1200px;
    overflow: hidden;
    background: var(--backdrop);
    font-family: "Exo 2", sans-serif;
  }
  .card {
    position: absolute;
    left: 192px;
    width: 720px;
    height: 412px;
    box-shadow: 0 6px 18px rgba(0,0,0,0.45);
  }
  .card--front { top: 146px; background: var(--card-white); }
  .card--back { top: 602px; background: var(--card-black); }

  /* Front */
  .company-mark {
    position: absolute;
    top: 78px;
    left: 0;
    width: 100%;
    text-align: center;
  }
  .company-mark__name {
    font-size: 48px;
    font-weight: 600;
    letter-spacing: 1px;
    color: var(--ink);
    line-height: 1;
  }
  .company-mark__tagline {
    margin-top: 6px;
    font-size: 13px;
    font-weight: 500;
    letter-spacing: 2.5px;
    color: var(--ink);
    text-transform: uppercase;
  }
  .person {
    position: absolute;
    top: 196px;
    width: 100%;
    text-align: center;
  }
  .person__name {
    font-size: 27px;
    font-weight: 600;
    color: var(--accent-red);
    text-transform: uppercase;
    letter-spacing: 0.5px;
  }
  .person__role {
    margin-top: 2px;
    font-size: 19px;
    font-weight: 400;
    color: var(--ink);
  }
  .contact-band {
    position: absolute;
    top: 272px;
    left: 0;
    width: 720px;
    height: 92px;
  }
  .contact-band__shape { position: absolute; inset: 0; }
  .contact-list {
    position: absolute;
    left: 42px;
    top: 19px;
    list-style: none;
    color: var(--card-white);
    font-size: 19px;
  }
  .contact-list li {
    display: flex;
    align-items: center;
    gap: 10px;
    height: 28px;
  }
  .contact-list svg { width: 18px; height: 18px; fill: var(--accent-red); }
  .contact-address {
    position: absolute;
    right: 44px;
    top: 21px;
    text-align: right;
    color: var(--card-white);
    font-size: 19px;
    line-height: 28px;
    font-style: normal;
  }
  .card-site--front {
    position: absolute;
    top: 370px;
    width: 100%;
    text-align: center;
    font-size: 18px;
    letter-spacing: 4px;
    color: var(--ink-soft);
  }

  /* Back */
  .brand-row {
    position: absolute;
    top: 180px;
    left: 0;
    width: 100%;
    display: flex;
    justify-content: center;
    align-items: center;
    gap: 34px;
  }
  .brand {
    display: flex;
    align-items: center;
    gap: 8px;
    font-size: 26px;
    font-weight: 600;
    line-height: 1;
  }
  .brand--fen { color: var(--card-white); font-size: 40px; }
  .brand--tavapuni { color: var(--brand-grey); }
  .brand--elmstretch { color: var(--brand-plum); }
  .brand--grit { color: var(--accent-red); }
  .brand__dot {
    width: 16px; height: 16px; border-radius: 50%;
    border: 3px solid var(--brand-grey);
  }
  .card-site--back {
    position: absolute;
    top: 336px;
    width: 100%;
    text-align: center;
    font-size: 20px;
    font-style: italic;
    letter-spacing: 9px;
    color: var(--card-white);
  }
</style>
</head>
<body>

<section class="card card--front">
  <div class="company-mark">
    <div class="company-mark__name">FEN ATHLETICS</div>
    <div class="company-mark__tagline">Performance Wear</div>
  </div>

  <div class="person">
    <div class="person__name">Owen Hartley</div>
    <div class="person__role">Managing Director</div>
  </div>

  <div class="contact-band">
    <svg class="contact-band__shape" viewBox="0 0 720 92" preserveAspectRatio="none" aria-hidden="true">
      <polygon points="0,0 44,0 20,92 0,92" fill="var(--accent-red)"/>
      <path d="M52,0 H690 Q700,0 697,10 L676,82 Q673,92 662,92 H28 Q18,92 21,82 L42,10 Q45,0 52,0 Z" fill="var(--card-black)"/>
      <polygon points="706,0 720,0 720,60 690,92 682,92" fill="var(--accent-red)"/>
    </svg>
    <ul class="contact-list">
      <li>
        <svg viewBox="0 0 24 24" aria-hidden="true"><path d="M6.6 10.8c1.4 2.8 3.8 5.1 6.6 6.6l2.2-2.2c.3-.3.7-.4 1-.2 1.1.4 2.3.6 3.6.6.6 0 1 .4 1 1V20c0 .6-.4 1-1 1C10.6 21 3 13.4 3 4c0-.6.4-1 1-1h3.5c.6 0 1 .4 1 1 0 1.3.2 2.5.6 3.6.1.3 0 .7-.2 1l-2.3 2.2z"/></svg>
        +44 (0)1632 960418
      </li>
      <li>
        <svg viewBox="0 0 24 24" aria-hidden="true"><path d="M2 5h20v14H2z M2 5l10 8 10-8" /></svg>
        owen@fenathletics.co.uk
      </li>
    </ul>
    <address class="contact-address">
      Kestrel Park, Lowfield<br>
      Ashby, LN4 7QT
    </address>
  </div>

  <div class="card-site card-site--front">www.fenathletics.co.uk</div>
</section>

<section class="card card--back">
  <div class="brand-row">
    <span class="brand brand--fen">Fen</span>
    <span class="brand brand--tavapuni"><span class="brand__dot"></span>TavaPuni</span>
    <span class="brand brand--elmstretch">ElmStretch</span>
    <span class="brand brand--grit">Grit and Rain</span>
  </div>
  <div class="card-site card-site--back">www.fenathletics.co.uk</div>
</section>

</body>
</html>
```